Upstart Retirement Planning Firm needs help with business card design

Harborview Nest Advisors, LLC is looking for help with business card design. We give advice on investments, insurance, and other financial matters related to retirement. There are some required disclosures that we will provide but mostly we are looking for a professional, classy business card that reflects the theme we have chosen. We have a logo that is attached but we would like to add a phrase; "Turning Your Earned Income Into Retirement Income"

Doubled sided only so that we can add the required disclosures (needed for our industry) on the back of the card. We will provide the exact words for this in 1-2 days.

Target Market(s)

Retirees and Pre-retirees. Professionals 50+ years old

Industry/Entity Type

Financial Planning

Contact Information for Business Card

We currently have two people who will need separate cards so we'd like to have a template so that we can add names for new cards in the future.

For the first run, please show the following information.

Gregor Pelham, MBA, ChFC®, CLU®
Financial Advisor, Registered Representative
gpelham@harborviewnest.example
Phone: (555) 318-2946
Toll Free Fax: (800) 555-0193

Address is
2187 Meadowlark Ridge Rd.
Suite K418
Virginia Beach, VA 23999

Colors
3277b5

Requirements
Must have
• Logo, contact info, small phase to describe business (in description), required legal disclosures on back of the card as follows (in small font)
• Gregor Pelham is a registered representative of and offers securities through Brightmoor Capital Brokerage Corporation, Member FNQX. Brightmoor Capital Brokerage Corporation is a member of the Brightmoor Capital Alliance which is the marketing name for Brightmoor Holding Corporation and its affiliates.
Nice to have
• Rounded edges, raised letters
Should not have
• any colors that aren't in the logo (other than black for font)

```html
<!DOCTYPE html>
<html lang="en">
<head>
<meta charset="utf-8">
<title>Harborview Nest Advisors, LLC — Business Card</title>
<link rel="stylesheet" href="https://fonts.googleapis.com/css2?family=Libre+Baskerville:ital,wght@0,400;0,700;1,400&display=swap">
<style>
  :root {
    --brand-blue: #3277b5;
    --deep-blue: #2d5fa6;
    --logo-grey: #8f8f8f;
    --band-grey: #c9c9c9;
    --band-grey-light: #e2e2e2;
    --ink: #1e1e1e;
    --ink-soft: #444444;
    --paper: #fbfbfb;
    --stage: #efefef;
  }
  * { box-sizing: border-box; margin: 0; padding: 0; }
  html, body {
    width: 1200px; height: 892px; overflow: hidden;
    background: var(--stage);
    font-family: "Libre Baskerville", "Times New Roman", serif;
  }
  .canvas {
    width: 1200px; height: 892px;
    display: flex; flex-direction: column; align-items: center; justify-content: center;
    gap: 30px;
  }
  .card {
    width: 700px; height: 400px;
    background: var(--paper);
    border-radius: 14px;
    position: relative;
    overflow: hidden;
    box-shadow: 0 2px 10px rgba(0,0,0,0.12);
  }

  /* Contact side */
  .card--front .brand {
    position: absolute; top: 40px; right: 50px;
    display: flex; flex-direction: column; align-items: flex-end;
  }
  .brand__row { display: flex; align-items: center; gap: 12px; }
  .brand__name { color: var(--brand-blue); font-size: 21px; letter-spacing: 0.5px; }
  .brand__dot {
    width: 14px; height: 14px; border-radius: 50%;
    background: var(--brand-blue);
  }
  .brand__rule {
    width: 270px; height: 1px; background: var(--logo-grey); margin-top: 10px;
  }
  .card--front .details {
    position: absolute; top: 128px; left: 0; right: 0;
    display: flex;
  }
  .identity {
    width: 300px; padding-right: 24px;
    text-align: right;
    border-right: 1px solid var(--brand-blue);
    padding-top: 4px; padding-bottom: 26px;
  }
  .identity__name { color: var(--brand-blue); font-size: 20px; margin-bottom: 8px; }
  .identity__line { color: var(--ink-soft); font-size: 15px; line-height: 1.5; }
  .contact { padding-left: 22px; padding-top: 34px; }
  .contact__row {
    display: flex; align-items: flex-start; gap: 12px;
    font-size: 15.5px; color: var(--ink); line-height: 1.45;
  }
  .contact__icon {
    flex: none; width: 15px; height: 15px; margin-top: 4px;
    background: var(--brand-blue); border-radius: 2px;
    display: flex; align-items: center; justify-content: center;
  }
  .contact__icon svg { width: 10px; height: 10px; }
  .band {
    position: absolute; left: 0; right: 0; bottom: 0; height: 56px;
    background: linear-gradient(180deg, var(--band-grey-light), var(--band-grey));
    border-top: 3px solid var(--brand-blue);
  }

  /* Logo side */
  .card--back { background: var(--deep-blue); padding: 16px; }
  .card--back .face {
    width: 100%; height: 100%;
    background: var(--paper);
    border-radius: 4px;
    display: flex; flex-direction: column; align-items: center; justify-content: center;
    padding: 0 40px;
  }
  .card--back .brand__row { gap: 16px; margin-top: 30px; }
  .card--back .brand__name { font-size: 30px; letter-spacing: 0.6px; }
  .card--back .brand__dot { width: 22px; height: 22px; }
  .card--back .brand__rule { width: 460px; margin-top: 14px; }
  .tagline {
    margin-top: 14px;
    color: var(--ink-soft); font-size: 14px; letter-spacing: 0.4px;
  }
  .disclosure {
    margin-top: auto; margin-bottom: 20px;
    color: var(--ink-soft); font-size: 9px; line-height: 1.5; text-align: center;
  }
</style>
</head>
<body>
<main class="canvas">

  <section class="card card--front" aria-label="Business card, contact side">
    <div class="brand">
      <div class="brand__row">
        <span class="brand__dot"></span>
        <span class="brand__name">Harborview Nest Advisors, LLC</span>
      </div>
      <span class="brand__rule"></span>
    </div>

    <div class="details">
      <div class="identity">
        <p class="identity__name">Gregor Pelham, MBA</p>
        <p class="identity__line">ChFC®, CLU®</p>
        <p class="identity__line">Financial Advisor</p>
        <p class="identity__line">Registered Representative</p>
      </div>

      <div class="contact">
        <p class="contact__row">
          <span class="contact__icon"><svg viewBox="0 0 10 10"><path d="M2 1 L4 1 L4.6 3 L3.5 4 Q4.5 6 6 6.5 L7 5.4 L9 6 L9 8 Q8.6 9 7.5 9 Q1 8.3 1 2.5 Q1 1 2 1Z" fill="#fff"/></svg></span>
          <span>(555) 318-2946</span>
        </p>
        <p class="contact__row">
          <span class="contact__icon"><svg viewBox="0 0 10 10"><path d="M2 1 L4 1 L4.6 3 L3.5 4 Q4.5 6 6 6.5 L7 5.4 L9 6 L9 8 Q8.6 9 7.5 9 Q1 8.3 1 2.5 Q1 1 2 1Z" fill="#fff"/></svg></span>
          <span>(800) 555-0193</span>
        </p>
        <p class="contact__row">
          <span class="contact__icon"><svg viewBox="0 0 10 10"><rect x="1" y="2.5" width="8" height="5.5" fill="none" stroke="#fff" stroke-width="1"/><path d="M1 2.5 L5 5.5 L9 2.5" fill="none" stroke="#fff" stroke-width="1"/></svg></span>
          <span>gpelham@harborviewnest.example</span>
        </p>
        <p class="contact__row">
          <span class="contact__icon"><svg viewBox="0 0 10 10"><path d="M5 9.5 Q1.8 5.6 1.8 3.8 A3.2 3.2 0 0 1 8.2 3.8 Q8.2 5.6 5 9.5Z" fill="#fff"/><circle cx="5" cy="3.8" r="1.2" fill="#3277b5"/></svg></span>
          <span>2187 Meadowlark Ridge Rd. Suite<br>K418 Virginia Beach, VA 23999</span>
        </p>
      </div>
    </div>

    <div class="band"></div>
  </section>

  <section class="card card--back" aria-label="Business card, logo side">
    <div class="face">
      <div class="brand__row">
        <span class="brand__dot"></span>
        <span class="brand__name">Harborview Nest Advisors, LLC</span>
      </div>
      <span class="brand__rule"></span>
      <p class="tagline">Turning Your Earned Income Into Retirement Income</p>
      <p class="disclosure">Gregor Pelham is a registered representative of and offers securities through Brightmoor Capital Brokerage Corporation, Member FNQX. Brightmoor Capital Brokerage Corporation is a member of the Brightmoor Capital Alliance which is the marketing name for Brightmoor Holding Corporation and its affiliates.</p>
    </div>
  </section>

</main>
</body>
</html>
```